Web Design For Staffing Company

We need a homepage web design for a technical staffing company.

Please see attached brief for project details.

please make the site modern with bold colors while matching the logo

Be sure to read the attached breif in full beforehand.

Target Market(s)

technical companies looking to hire talent

Industry/Entity Type

Staffing

Number of Pages Required

1 page

Font styles to use
Sans Serif

```html
<!DOCTYPE html>
<html lang="en">
<head>
<meta charset="utf-8">
<title>Veltrix Staffing – Technical Staffing</title>
<link href="https://fonts.googleapis.com/css2?family=Mulish:ital,wght@0,400;0,600;0,700;0,800;1,400&family=Oswald:wght@400&display=swap" rel="stylesheet">
<style>
:root{
  --blue:#1a8fd1;
  --blue-deep:#0f6fae;
  --black:#000;
  --ink:#1c1c1c;
  --muted:#555;
  --light:#f4f4f4;
  --white:#fff;
  --star:#f5b50a;
}
*{margin:0;padding:0;box-sizing:border-box}
html,body{width:1200px;height:3661px;overflow:hidden}
body{position:relative;font-family:"Mulish",sans-serif;color:var(--ink);background:var(--white)}
.abs{position:absolute}
.btn{position:absolute;display:flex;align-items:center;justify-content:center;gap:7px;font:700 13px "Mulish",sans-serif;letter-spacing:.6px;color:var(--white);text-transform:uppercase}
.btn.dark{background:var(--black)}
.btn.blue{background:var(--blue)}
.brand{font:800 30px "Mulish",sans-serif;color:var(--blue-deep);display:flex;align-items:center;gap:9px}
.brand i{display:block;width:16px;height:16px;border-radius:50%;background:var(--blue)}
/* header */
.site-header{top:0;left:0;width:1200px;height:98px;background:var(--white)}
.nav{top:41px;font:600 13px "Mulish",sans-serif;letter-spacing:.4px;color:#222}
.nav.active{color:var(--blue)}
.search{left:867px;top:28px;width:192px;height:40px;border:1px solid #ddd;font-size:11px;color:#888;padding:13px 0 0 16px}
/* hero */
.hero{top:98px;left:0;width:1200px;height:592px;background:linear-gradient(120deg,#c9c3bb 0%,#a39d96 40%,#6e6963 75%,#2d3440 100%)}
.hero-title{top:498px;left:0;width:1200px;text-align:center;font:400 40px/50px "Oswald",sans-serif;color:var(--white);text-shadow:0 2px 6px rgba(0,0,0,.35)}
.intro{top:765px;left:230px;width:740px;text-align:center;font:400 18.5px/31px "Mulish",sans-serif;color:#333}
.intro mark{background:var(--blue);color:var(--white);font-weight:700;padding:2px 8px}
/* services */
.band{top:935px;left:0;width:1200px;height:379px;background:linear-gradient(90deg,#1a8fd1,#2a9ad6 50%,#1683c4)}
.card{position:absolute;top:1021px;width:432px;height:617px;background:var(--white);box-shadow:0 4px 14px rgba(0,0,0,.08)}
.card .photo{height:293px}
.card .body{position:absolute;left:32px;top:330px;width:375px;font-size:12.5px;line-height:22px;color:#333}
.card h3{font:700 17.5px "Mulish",sans-serif;letter-spacing:.5px;margin-bottom:10px}
.card h3 span{color:var(--blue)}
.card p{margin-bottom:9px}
/* testimonial */
.sec-title{left:0;width:1200px;text-align:center;font:700 28px "Mulish",sans-serif;letter-spacing:1px}
.sec-title span{color:var(--blue)}
.quote{top:1797px;left:285px;width:630px;text-align:center;font:italic 400 16px/26.5px "Mulish",sans-serif;color:#222}
.qmark{font:800 90px/1 "Mulish",sans-serif;color:#9fd0ee}
/* blog */
.blog-bg{top:2100px;left:0;width:1200px;height:691px;background:var(--light)}
.post{position:absolute;top:2236px;width:293px;height:393px;background:var(--white);box-shadow:0 3px 10px rgba(0,0,0,.06)}
.post .photo{height:178px}
.post .meta{display:flex;justify-content:space-between;padding:20px 16px 0;font-size:13px}
.post .meta b{color:var(--blue);font-weight:600}
.post .meta span{color:#666;font-weight:600}
.post h4{padding:10px 16px 0;font:700 14px/21px "Mulish",sans-serif}
.post p{padding:8px 16px 0;font-size:12px;line-height:22px;color:#555}
.post a{display:block;padding:4px 16px 0;font-size:12.5px;font-weight:700;color:var(--blue);text-decoration:underline}
.arrow{width:42px;height:42px;border-radius:50%;background:var(--white);box-shadow:0 2px 8px rgba(0,0,0,.12);display:flex;align-items:center;justify-content:center}
/* cta */
.cta{position:absolute;top:2876px;width:443px;height:282px;color:var(--white)}
.cta h3{position:absolute;left:33px;top:140px;width:380px;font:700 23px/29px "Mulish",sans-serif}
.cta svg{position:absolute;left:33px;top:38px}
/* footer */
.footer{top:3249px;left:0;width:1200px;height:367px}
.foot-col{top:3385px;color:var(--white)}
.foot-col h5{font:700 16.5px "Mulish",sans-serif;letter-spacing:.5px;margin-bottom:16px}
.foot-col p{font-size:12.5px;line-height:18px;color:#ddd}
.bottom{top:3616px;left:0;width:1200px;height:45px;background:var(--blue);color:var(--white);font-size:12px;padding:14px 0 0 142px}
.social{top:3627px;width:24px;height:24px;border:1.5px solid var(--white);border-radius:50%}
</style>
</head>
<body>

<header class="site-header abs">
  <div class="brand abs" style="left:142px;top:30px"><i></i>Veltrix</div>
  <span class="nav abs active" style="left:444px">HOME</span>
  <span class="nav abs" style="left:509px">ABOUT</span>
  <span class="nav abs" style="left:581px">JOB SEEKERS</span>
  <span class="nav abs" style="left:698px">CLIENTS</span>
  <span class="nav abs" style="left:778px">CONTACT</span>
  <div class="search abs">Search
    <svg class="abs" style="right:12px;top:12px" width="16" height="16" viewBox="0 0 16 16"><circle cx="6.5" cy="6.5" r="5" fill="none" stroke="#1a8fd1" stroke-width="2.2"/><line x1="10.3" y1="10.3" x2="15" y2="15" stroke="#1a8fd1" stroke-width="2.4"/></svg>
  </div>
</header>

<section class="hero abs" role="img" aria-label="Photo of smiling colleagues in a bright office meeting"></section>
<h1 class="hero-title abs">The Right People For The Right Jobs!<br>Bridging the talent gap in Technical Staffing</h1>
<a class="btn dark" style="left:449px;top:614px;width:141px;height:43px">Hire Talent</a>
<a class="btn blue" style="left:610px;top:614px;width:141px;height:43px">Get Hired</a>

<p class="intro abs"><mark>Veltrix Staffing</mark> is a National Technical Staffing and Recruiting Solutions Provider founded in2013 focused on matching contract and full time Engineering and IT professionals with new andexciting employment opportunities!</p>

<div class="band abs" role="img" aria-label="Blue tinted photo of professionals shaking hands"></div>

<article class="card" style="left:141px">
  <div class="photo" role="img" aria-label="Photo of a team meeting around a glass table" style="background:linear-gradient(135deg,#cdd6dc,#8d99a3 60%,#5a6570)"></div>
  <div class="body">
    <h3>SIMPLY SAID... <span>WE LOVE TO RECRUIT!</span></h3>
    <p style="font-size:13.5px">It's our passion and we take it very seriously!</p>
    <p>It is not easy for JOB SEEKERS to put their job search efforts and trust in the hands of someone else, especially when there are so many Staffing Firms to choose from.</p>
    <p>So how do you know you are choosing the best Staffing Representation possible?</p>
  </div>
  <a class="btn dark" style="left:32px;top:543px;width:125px;height:38px">Learn More</a>
  <a class="btn blue" style="left:174px;top:543px;width:125px;height:38px">View Jobs</a>
</article>

<article class="card" style="left:627px">
  <div class="photo" role="img" aria-label="Photo of two colleagues talking at a desk" style="background:linear-gradient(135deg,#e2e4e2,#b3aea6 55%,#6f6a66)"></div>
  <div class="body" style="top:328px">
    <p style="margin-bottom:2px">Are you responsible for Technical Staffing within your organization?</p>
    <p style="margin-bottom:2px">Are you satisfied with your current Supplier(s)' overall performance?</p>
    <p style="margin-bottom:2px">Does it appear they identify potential Candidate(s) based purely on "buzz-word" searches?</p>
    <p>Is it evident they just do not grasp the scope and responsibilities of your technical staffing need(s)?</p>
  </div>
  <a class="btn dark" style="left:32px;top:543px;width:125px;height:38px">Learn More</a>
  <a class="btn blue" style="left:174px;top:543px;width:125px;height:38px">Hire Talent</a>
</article>

<h2 class="sec-title abs" style="top:1718px">CUSTOMER <span>TESTIMONIALS</span></h2>
<div class="qmark abs" style="left:228px;top:1758px">&ldquo;</div>
<p class="quote abs">Mark Dalen is an excellent recruiter. He is articulate, honest, has a good nature and is aneffective information conduit between his clients and candidates. He gave me the feeling he is there for the big picture desiring to forge a future relationship that will be mutually beneficial toboth of us.</p>
<div class="qmark abs" style="left:896px;top:1872px">&rdquo;</div>
<div class="abs" style="left:356px;top:1922px;width:488px;height:1px;background:#bbb"></div>
<svg class="abs" style="left:594px;top:1922px" width="12" height="7"><path d="M0 0 L6 7 L12 0Z" fill="#bbb"/></svg>
<div class="abs" style="top:1945px;left:0;width:1200px;text-align:center;font:700 16px 'Mulish',sans-serif">SAM R</div>
<div class="abs" style="top:1970px;left:0;width:1200px;text-align:center;font-size:12px;color:#333">Electrical Test Engineer in the Automotive Sector</div>
<svg class="abs" style="left:548px;top:1995px" width="104" height="20" viewBox="0 0 104 20">
  <g fill="#f5b50a"><path id="s" d="M9 1l2.4 5.3 5.6.5-4.3 3.8 1.3 5.6L9 13.3 4 16.2l1.3-5.6L1 6.8l5.6-.5z"/><use href="#s" x="22"/><use href="#s" x="44"/><use href="#s" x="66"/><use href="#s" x="88"/></g>
</svg>

<div class="blog-bg abs"></div>
<h2 class="sec-title abs" style="top:2176px">LATEST <span>BLOGS</span></h2>
<div class="arrow abs" style="left:69px;top:2393px"><svg width="18" height="14"><path d="M17 7H2M7 1L1 7l6 6" fill="none" stroke="#1a8fd1" stroke-width="2"/></svg></div>
<div class="arrow abs" style="left:1088px;top:2393px"><svg width="18" height="14"><path d="M1 7h15M11 1l6 6-6 6" fill="none" stroke="#1a8fd1" stroke-width="2"/></svg></div>

<article class="post" style="left:141px">
  <div class="photo" role="img" aria-label="Black and white portrait photo with a quote overlay" style="background:linear-gradient(90deg,#6a6a6a,#2b2b2b 55%,#111)"></div>
  <div class="meta"><b>June 19, 2019</b><span>by veltrixstaffing</span></div>
  <h4>Tips for Spotting a U.S. Recession Before It Becomes Official</h4>
  <p>As the U.S. nears a record-long expansion in July, the conversation is increasingly turning to when it will all end.</p>
  <a>READ MORE</a>
</article>
<article class="post" style="left:454px">
  <div class="photo" role="img" aria-label="Photo of a woman working on a laptop" style="background:linear-gradient(135deg,#d9d3c6,#8a8074 55%,#2e2c2a)"></div>
  <div class="meta"><b>June 17, 2019</b><span>by veltrixstaffing</span></div>
  <h4>Ways To Make The Most Of The Hot Job Market</h4>
  <p>This is the tightest labor market I can remember. Unemployment is at a 50-year low and wage growth is at 3.2%," said</p>
  <a>READ MORE</a>
</article>
<article class="post" style="left:766px">
  <div class="photo" role="img" aria-label="Photo of a business handshake over a desk" style="background:linear-gradient(135deg,#3f6f9a,#9cb6cc 50%,#dfe7ee)"></div>
  <div class="meta"><b>June 6, 2019</b><span>by veltrixstaffing</span></div>
  <h4>Back To Basics: Meeting Employees' Needs To Improve Organizational...</h4>
  <p>The benefits of employee satisfaction are well-established, so HR professionals and leaders across all industries spend a</p>
  <a>READ MORE</a>
</article>
<a class="btn blue" style="left:546px;top:2667px;width:108px;height:39px">View All</a>

<div class="cta" style="left:141px;background:linear-gradient(135deg,#1c93d6,#1580c2)" role="img" aria-label="Blue tinted photo of a smiling professional">
  <svg width="84" height="76" viewBox="0 0 84 76" fill="none" stroke="#fff" stroke-width="2.4"><circle cx="42" cy="16" r="10"/><path d="M26 72V46a16 16 0 0 1 32 0v26M38 44l4 10 4-10"/><circle cx="16" cy="26" r="8"/><path d="M2 72V52a14 14 0 0 1 22-11"/><circle cx="68" cy="26" r="8"/><path d="M82 72V52a14 14 0 0 0-22-11"/></svg>
  <h3>Looking For Career-minded<br>Candidates?</h3>
  <a class="btn dark" style="left:33px;top:209px;width:161px;height:37px">Request Talent</a>
</div>
<div class="cta" style="left:616px;background:linear-gradient(135deg,#2c2f33,#1c1e21)" role="img" aria-label="Dark tinted photo of people in an office">
  <svg width="80" height="76" viewBox="0 0 80 76" fill="none" stroke="#fff" stroke-width="2.4"><circle cx="30" cy="20" r="13"/><path d="M4 74V56a26 22 0 0 1 46-10"/><rect x="44" y="50" width="32" height="22"/><path d="M54 50v-6h12v6M44 60h32"/></svg>
  <h3>Looking For Career-minded<br>Candidates?</h3>
  <a class="btn blue" style="left:33px;top:209px;width:130px;height:37px">Search Jobs</a>
</div>

<svg class="footer abs" width="1200" height="367" viewBox="0 0 1200 367">
  <path d="M0 110 C300 -30 900 -30 1200 110 V367 H0Z" fill="#000"/>
  <path d="M0 104 C300 -36 900 -36 1200 104" fill="none" stroke="#1a8fd1" stroke-width="5"/>
</svg>
<div class="foot-col abs" style="left:142px;width:160px">
  <h5>FIND JOBS</h5><p>Search Our extensive list of available jobs to find your match.</p>
</div>
<div class="foot-col abs" style="left:337px;width:210px">
  <h5>REQUEST AN EMPLOYEE</h5><p>We're here to provide the people you need to get work done.</p>
</div>
<div class="foot-col abs" style="left:596px;width:200px">
  <h5>GET IN TOUCH</h5>
  <p style="padding-left:17px;position:relative"><svg class="abs" style="left:0;top:2px" width="10" height="14" viewBox="0 0 10 14"><path d="M5 14S0 8 0 5a5 5 0 0 1 10 0c0 3-5 9-5 9z" fill="#1a8fd1"/><circle cx="5" cy="5" r="2" fill="#000"/></svg>120 Harbor Lane, Suite 2,<br>3rd floor Riverton,<br>MA 01999</p>
  <p style="padding-left:17px;position:relative;margin-top:8px"><svg class="abs" style="left:0;top:3px" width="11" height="11" viewBox="0 0 11 11"><path d="M2 0l2 3-1 1.5a7 7 0 0 0 3.5 3.5L8 7l3 2-1.5 2C4 11 0 7 0 1.5z" fill="#1a8fd1"/></svg>555-014-2290</p>
</div>
<a class="btn blue" style="left:142px;top:3520px;width:136px;height:39px"><svg width="13" height="13"><circle cx="5.5" cy="5.5" r="4" fill="none" stroke="#fff" stroke-width="2"/><line x1="8.5" y1="8.5" x2="12" y2="12" stroke="#fff" stroke-width="2"/></svg>Search Now</a>
<a class="btn blue" style="left:337px;top:3520px;width:136px;height:39px"><svg width="12" height="13"><circle cx="6" cy="3.5" r="3.2" fill="#fff"/><path d="M0 13a6 5.5 0 0 1 12 0z" fill="#fff"/></svg>Start Today</a>
<a class="btn blue" style="left:592px;top:3520px;width:136px;height:39px"><svg width="14" height="10"><rect width="14" height="10" fill="#fff"/><path d="M0 0l7 6 7-6" fill="none" stroke="#1a8fd1" stroke-width="1.5"/></svg>Contact Us</a>
<div class="brand abs" style="left:840px;top:3450px;color:#d8d8d8;font-size:40px"><i style="width:20px;height:20px;background:#bbb"></i>Veltrix</div>

<footer class="bottom abs">Copyright © 2020 Veltrix Staffing. All Rights Reserved.</footer>
<div class="social abs" style="left:964px"></div>
<div class="social abs" style="left:998px"></div>
<div class="social abs" style="left:1033px"></div>

</body>
</html>
```